Envelope Design Project

I will need two envelopes to be designed:-

DL size
C4 size

Please see uploaded documents for Design specs:

1) Design specs provided by printer (doc called DL Envelope Specs)
2) Design specs to comply with Kestrel Courier requirements (doc called Kestrel Courier Envelope Design Requirements)

Please adhere to the above for final design. Many thanks.

Target Market(s)

Real Estate Agents, Strata Managers, Builders, Architects, Business Owners

Industry/Entity Type

Printer

Requirements
Must have
• In top left corner
- Logo
- Return address - Suite 6, 19 Marlowe St, Brenvale, NSW 2187

```html
<!DOCTYPE html>
<html lang="en">
<head>
<meta charset="utf-8">
<title>Corvin Hazard Services – Envelope Set</title>
<link href="https://fonts.googleapis.com/css2?family=Questrial&display=swap" rel="stylesheet">
<style>
  :root {
    --navy: #13133a;
    --green: #6b922b;
    --paper-light: #ffffff;
    --paper-shade: #e4e4e6;
    --backdrop: #e9e9ec;
    --ink: #1d1d2b;
  }
  * { margin: 0; padding: 0; box-sizing: border-box; }
  html, body {
    width: 1200px;
    height: 900px;
    overflow: hidden;
  }
  body {
    background: var(--backdrop);
    font-family: "Questrial", "Century Gothic", sans-serif;
    position: relative;
  }
  .envelope {
    position: absolute;
    background: linear-gradient(160deg, var(--paper-light) 30%, var(--paper-shade) 100%);
    box-shadow: 0 14px 30px rgba(0, 0, 0, 0.22);
    overflow: hidden;
  }
  .envelope--dl { left: 90px; top: 70px; width: 460px; height: 230px; }
  .envelope--c4 { left: 440px; top: 330px; width: 660px; height: 466px; }

  .envelope__art {
    position: absolute;
    inset: 0;
    width: 100%;
    height: 100%;
  }
  .band { fill: var(--navy); }
  .corner { fill: var(--green); }

  .sender {
    position: absolute;
    color: var(--ink);
  }
  .envelope--dl .sender { left: 30px; top: 36px; }
  .envelope--c4 .sender { left: 62px; top: 76px; }

  .brand {
    color: var(--navy);
    font-weight: 400;
    letter-spacing: 0.02em;
    white-space: nowrap;
    line-height: 1.1;
  }
  .envelope--dl .brand { font-size: 16px; }
  .envelope--c4 .brand { font-size: 28px; }

  .return-address {
    font-style: normal;
    color: var(--ink);
    white-space: nowrap;
  }
  .envelope--dl .return-address { font-size: 7.5px; margin-top: 9px; }
  .envelope--c4 .return-address { font-size: 11px; margin-top: 14px; }
</style>
</head>
<body>

  <section class="envelope envelope--dl" aria-label="DL envelope">
    <svg class="envelope__art" viewBox="0 0 460 230" preserveAspectRatio="none" aria-hidden="true">
      <path class="corner" d="M460 140 V230 H402 Z"/>
      <path class="band" d="M0 192 H350 C380 192 396 204 408 230 H0 Z"/>
    </svg>
    <div class="sender">
      <div class="brand">Corvin Hazard Services</div>
      <address class="return-address">Suite 6, 19 Marlowe St, Brenvale, NSW 2187</address>
    </div>
  </section>

  <section class="envelope envelope--c4" aria-label="C4 envelope">
    <svg class="envelope__art" viewBox="0 0 660 466" preserveAspectRatio="none" aria-hidden="true">
      <path class="corner" d="M660 270 V466 H580 Z"/>
      <path class="band" d="M0 382 H500 C548 382 574 405 592 466 H0 Z"/>
    </svg>
    <div class="sender">
      <div class="brand">Corvin Hazard Services</div>
      <address class="return-address">Suite 6, 19 Marlowe St, Brenvale, NSW 2187</address>
    </div>
  </section>

</body>
</html>
```